Captivating packaging design for sports company.

We need a packaging design that encompasses our resistance bands workout set. Our focus is quality, convenience, and versatility. The design should be tailored to our broad array of customer across all paths. We would like the packaging to reflect our brand and product features such as: the LBS(weight) listed on each of the bands, convenience for travel and at home, highest quality, for all fitness levels, and free eBook. We'd also like to include a couple of our reviews on the packaging. Please refer to our listing on Varlo for additional information https://www.shopvarlo.com/Brisklane-Athletics-Resistance-Workout-Carrying/dp/K47TR2XMNQ/ref=sr_1_1?ie=UTF8&qid=1470453588&sr=8-1&keywords=brisklane+athletics+resistance+bands
Please reach out with additional questions for any further details. Thank you.
Target Market(s)
Sports, fitness, and health enthusiasts of all ages.
Industry/Entity Type
It Company
Look and feel
Each slider illustrates characteristics of the customer's brand and the style your logo design should communicate.

```html
<!DOCTYPE html>
<html lang="en">
<head>
<meta charset="utf-8">
<title>Brisklane Athletics Resistance Bands Packaging</title>
<link rel="stylesheet" href="https://fonts.googleapis.com/css2?family=Michroma&family=Orbitron:wght@700;900&display=swap">
<style>
  :root {
    --sky: #6aa7dc;
    --sky-light: #dbe8f5;
    --navy: #17508c;
    --ink: #111418;
    --white: #ffffff;
    --backdrop: #e6e7e9;
  }
  * { margin: 0; padding: 0; box-sizing: border-box; }
  html, body { width: 1200px; height: 1200px; overflow: hidden; }
  body {
    background: var(--backdrop);
    font-family: "Michroma", "Arial", sans-serif;
    color: var(--ink);
    position: relative;
  }
  .dieline {
    position: absolute;
    left: 110px; top: 170px;
    width: 980px; height: 860px;
    display: flex;
  }
  /* Side panel */
  .side-panel {
    width: 280px; height: 100%;
    background: var(--sky);
    position: relative;
    padding: 60px 22px 0;
  }
  .brand {
    display: flex; align-items: center; gap: 10px;
    font-family: "Michroma", sans-serif;
    color: var(--ink);
    line-height: 1.05;
  }
  .brand-dot { width: 34px; height: 34px; border-radius: 50%; background: var(--ink); flex: none; }
  .brand-name { font-size: 15px; letter-spacing: 0.5px; }
  .side-panel .brand-name { font-size: 13px; }
  .badge {
    width: 110px; height: 110px; border-radius: 50%;
    border: 2px solid var(--ink);
    margin: 50px auto 0;
  }
  .box-contents {
    margin-top: 28px;
    text-align: center;
    font-size: 13px;
    line-height: 1.7;
    letter-spacing: 0.6px;
  }
  .slogan {
    position: absolute; left: 0; right: 0; top: 510px;
    text-align: center;
    font-size: 44px;
    line-height: 1.3;
    letter-spacing: 2px;
  }
  .resistance-tag {
    position: absolute; left: 18px; right: 18px; bottom: 40px;
    height: 120px;
    background: var(--navy);
    color: var(--white);
    display: flex; align-items: center; justify-content: center;
    text-align: center;
    font-size: 15px; line-height: 1.4;
    font-family: "Orbitron", sans-serif; font-weight: 700;
  }
  /* Front panel */
  .front-panel {
    width: 700px; height: 100%;
    background: linear-gradient(120deg, var(--sky-light) 0%, #b3cfea 45%, var(--sky) 100%);
    position: relative;
  }
  .hero-photo {
    position: absolute; left: 0; top: 0; bottom: 0; width: 345px;
    background: linear-gradient(160deg, #5f86ad 0%, #2b3f55 55%, #1c2733 100%);
    opacity: 0.85;
  }
  .front-panel .brand {
    position: absolute; right: 70px; top: 100px;
    flex-direction: column; gap: 10px; text-align: center;
  }
  .front-panel .brand-dot { width: 52px; height: 52px; }
  .front-panel .brand-name { font-size: 20px; }
  .title-banner {
    position: absolute; right: 0; top: 300px;
    width: 380px; height: 165px;
    background: var(--navy);
    color: var(--white);
    padding: 28px 0 0 22px;
    font-family: "Orbitron", sans-serif; font-weight: 900;
  }
  .title-banner::after {
    content: ""; position: absolute; left: 0; right: 0; bottom: -10px;
    height: 10px; background: var(--ink);
  }
  .title-kicker { font-size: 20px; font-weight: 700; letter-spacing: 1px; }
  .title-main { font-size: 40px; line-height: 1.05; letter-spacing: 1px; margin-top: 4px; }
  .product-copy {
    position: absolute; left: 372px; top: 510px;
    font-size: 16px; line-height: 1.75; letter-spacing: 0.8px;
  }
  .product-copy p + p { margin-top: 20px; }
</style>
</head>
<body>
  <main class="dieline">
    <section class="side-panel">
      <div class="brand">
        <span class="brand-dot"></span>
        <span class="brand-name">BRISKLANE<br>ATHLETICS</span>
      </div>
      <div class="badge" role="img" aria-label="Partner badge"></div>
      <div class="box-contents">
        IN THE BOX<br>
        x1 YELLOW - 2-4LB<br>
        x1 GREEN - 4-6LB<br>
        x1 BLUE - 10-12LB<br>
        x1 RED - 15-20LB<br>
        x1 BLACK - 25-30LB<br>
        CARRY CASE<br>
        E-BOOK
      </div>
      <div class="slogan">TONE<br>BURN<br>BUILD</div>
      <div class="resistance-tag">UP TO 75LBS<br>OF TOTAL<br>RESISTANCE</div>
    </section>
    <section class="front-panel">
      <div class="hero-photo" role="img" aria-label="Silhouetted athlete in blue shirt and black shorts stretching a resistance band behind his shoulders"></div>
      <div class="brand">
        <span class="brand-dot"></span>
        <span class="brand-name">BRISKLANE<br>ATHLETICS</span>
      </div>
      <div class="title-banner">
        <div class="title-kicker">HIGH QUALITY</div>
        <div class="title-main">RESISTANCE<br>BANDS</div>
      </div>
      <div class="product-copy">
        <p>Brisklane Athletics<br>Resistance Band<br>Workout Set</p>
        <p>4 Colourful Bands<br>Door Anchor<br>2 Handles<br>2 Ankle Straps<br>Carrying Case</p>
      </div>
    </section>
  </main>
</body>
</html>
```